DL, Tri Fold Flyer - Wild Wonder Works

We need DL Tri Fold Brochure designed to print and distribute to primary schools in Australia advertising our exciting and educational science workshops.

Fun, exciting yet with a professional/educational edge. Similar to the feel of our website science shop www.wildwonderworks-demo.com.au and/or incursion page wildwonderworksvisits-demo.com.au

Design should be fresh, clean and simple, eye-catching with a sense of quality.

There needs to be visual interest with graphic elements and pictures to break up the text. To be print ready with bleed and cut lines indicated for printer. Roll fold, 2 -sided, and full colour.

The font cover image spills on to the back cover and needs to relate to the Discovery Fortnight theme for 2020: Innovations for the future of our oceans. Perhaps eye-catching offshore ocean turbines (with or without ocean life underneath)? Example images attached, can use an image from Pixelvault library.

This is a link to brochures printed in the past to give you an idea of design and layout.

Can use images of our presenters/kids on facebook page to break up text - www.facebook.com/wildwonderworksdemo

Please see the attached file WildWonderWorksBrochureDesignBrief2020 for complete text and layout requirements - this file is coming soon.

Target Market(s)

Primary School Teachers

Colors

Designer to choose colors to be used in the design.

Requirements
Must have
• 1. Eye-catching front image picture, spilling on to back cover
• 2. Quality feel
• 3. Images to break up text

```html
<!DOCTYPE html>
<html lang="en">
<head>
<meta charset="utf-8">
<title>Wild Wonder Works – Workshop Topics 2020</title>
<link href="https://fonts.googleapis.com/css2?family=Roboto+Slab:wght@400;700&family=Source+Sans+3:wght@300;400;700&display=swap" rel="stylesheet">
<style>
  :root{
    --navy:#2e3b96;
    --orange:#e8892b;
    --band:#ec9a3c;
    --sky:#2f8fd0;
    --red:#d71920;
    --body:#5a5a5a;
    --ocean-dark:#1f6fa8;
    --ocean-light:#6ec3e8;
    --ink-on-ocean:#1b2b4a;
    --white:#ffffff;
  }
  *{margin:0;padding:0;box-sizing:border-box}
  html,body{width:1200px;height:848px;overflow:hidden;background:var(--white)}
  body{font-family:"Source Sans 3",sans-serif;font-weight:300;color:var(--body);position:relative}
  .panel{position:absolute;top:0;height:848px}
  .panel--left{left:0;width:404px}
  .panel--middle{left:404px;width:400px;padding:16px 8px 0 12px}
  .panel--right{left:804px;width:396px}
  .panel--right::before{content:"";position:absolute;left:0;top:0;width:1px;height:848px;background:#d9d9d9}

  .hero-photo{position:absolute;left:0;top:0;width:404px;height:234px;
    background:linear-gradient(135deg,#f2d35a 0%,#e7b441 40%,#c99a5a 70%,#8fa2b6 100%)}
  .hero-name{position:absolute;left:22px;top:40px;width:150px;font-family:"Roboto Slab",serif;
    font-weight:700;font-size:19px;line-height:21px;color:var(--white)}
  .hero-name-dot{display:inline-block;width:12px;height:12px;border-radius:50%;background:var(--white);margin-bottom:4px}

  .intro{position:absolute;left:20px;top:240px;width:372px}
  .intro h1{font-family:"Roboto Slab",serif;font-weight:700;font-size:17.6px;line-height:20.5px;color:var(--navy);margin-bottom:8px}
  .intro p{font-size:10.6px;line-height:12px}

  .topics-band{position:absolute;left:0;top:410px;width:404px;height:32px;background:var(--band);
    color:var(--white);font-size:18px;font-weight:400;text-align:center;line-height:32px;letter-spacing:.3px}

  .topics{position:absolute;left:20px;top:450px;width:374px}

  .section-title{font-family:"Roboto Slab",serif;font-weight:400;font-size:13.5px;line-height:16px;margin-bottom:3px}
  .section-title--orange{color:var(--orange)}
  .section-title--sky{color:var(--sky)}
  .section-title--navy{color:var(--navy)}

  .topic{margin-bottom:5px}
  .topic h3{font-family:"Roboto Slab",serif;font-weight:400;font-size:12.2px;line-height:13.5px}
  .topic p{font-size:10.6px;line-height:12px}
  .topic .states{color:var(--red)}
  .topic strong{font-weight:700;color:#222}
  .topic--navy h3{color:var(--navy)}
  .topic--orange h3{color:var(--orange)}
  .topic--sky h3{color:var(--sky)}

  .ocean-photo{position:absolute;left:1px;top:0;width:395px;height:750px;
    background:linear-gradient(180deg,var(--ocean-dark) 0%,#3b9bd4 35%,var(--ocean-light) 60%,#4aa7d8 85%,#2e86c0 100%)}
  .ocean-content{position:absolute;left:12px;top:12px;width:376px;color:var(--ink-on-ocean)}
  .ocean-content .topic p{color:var(--ink-on-ocean)}
  .ocean-content .topic h3{color:#3a43a0}
  .label-box{display:inline-block;background:var(--white);padding:2px 10px;margin-left:-11px;margin-bottom:3px}
  .label-box .section-title{margin:0;color:var(--sky)}
  .stem-band{position:absolute;left:1px;top:395px;width:395px;height:23px;background:var(--white);
    padding-left:11px;font-family:"Roboto Slab",serif;font-weight:700;font-size:13.5px;line-height:23px;color:var(--navy)}
  .stem-list{position:absolute;left:12px;top:420px;width:376px}
  .stem-list .topic p{color:var(--ink-on-ocean)}
  .stem-list .topic h3{color:var(--white)}
  .reactive{position:absolute;left:12px;top:752px;width:376px}
</style>
</head>
<body>

<section class="panel panel--left">
  <div class="hero-photo" role="img" aria-label="Smiling primary school students in yellow uniforms doing a hands-on science experiment"></div>
  <div class="hero-name"><span class="hero-name-dot"></span><br>Wild Wonder Works in Schools</div>

  <div class="intro">
    <h1>In 2020, our seriously FUN workshops will be available in VIC, QLD and NSW!</h1>
    <p>Our quality science incursions are aligned with the Curriculum, and blend enticing class demonstrations with hands-on experiments to facilitate genuine learning. Our expert workshop facilitators present a range of incursion topics encompassing biological, chemical, Earth &amp; space, and physical sciences as well as STEM workshops, from foundation to level 6. During our sessions students develop critical and creative thinking skills, they will ask questions, make predictions and draw conclusions using scientific methods.<br>The 2020 National Discovery Fortnight Theme is Deep Blue: Innovations for the future of our oceans. Our new workshop The Power of the Deep Blue has been developed around this theme.</p>
  </div>

  <div class="topics-band">WORKSHOP TOPICS</div>

  <div class="topics">
    <h2 class="section-title section-title--orange">CHEMICAL SCIENCES</h2>
    <article class="topic topic--navy"><h3>Chemistry Chaos - Foundation to Level 6</h3>
      <p>Colour changes, smoke, fizz and foam! Everything in our world is made-up of chemicals: explore interesting polymer chemicals, chemical reactions, reversible physical changes and more. Available in a junior or senior format. <span class="states">VIC, NSW, QLD</span></p></article>
    <article class="topic topic--navy"><h3>The Matter Of Matter - Level 3 to 6</h3>
      <p>Use the magic of dry ice to explore the three common states of matter - solids, liquids and gasses. From everlasting bubbling fountains to cool chemical fire extinguishers. This session matters! Available in a 90 minute format only. Incurs a $45 per day dry ice surcharge. <span class="states">VIC, NSW, QLD</span></p></article>
    <article class="topic topic--navy"><h3>Forensic Detective – Level 3 to 6</h3>
      <p>Can you crack the case and catch the thief!? Use real forensic science techniques, like PH tests, ink chromatography, glow chemicals, and fingerprint dusting to pin point the culprit. Available in a 90 minute format only. <span class="states">VIC, NSW, QLD</span></p></article>
    <article class="topic topic--navy"><h3>Super Bubble Science – Foundation to Level 2</h3>
      <p>Bubbles are more than trapped air in a film of soapy water. Their exact spherical shape and swirling rainbow colours make them a wonder of science. By this session’s end, you’ll be a true bubblogist. <span class="states">VIC, NSW, QLD</span></p></article>
    <article class="topic topic--navy"><h3>Kitchen Chemistry – Foundation to Level 2</h3>
      <p>A fun food workshop challenging you to think about everyday food in a whole new way. Experiment with a variety of food-related chemicals, and you even get to take home a bag of sweet, tongue tingling sherbet! <span class="states">VIC, NSW, QLD</span></p></article>
    <article class="topic topic--navy"><h3>Material Science – Foundation to Level 6</h3>
      <p>Explore the world around you - sort, classify and test the physical properties of natural and processed materials. Discover how materials can change physically as well as chemically. Mix a material concoction for a purpose, explore the effect of heat on materials, material waste and remake a material into a new product. <span class="states">VIC, NSW, QLD</span></p></article>
  </div>
</section>

<section class="panel panel--middle">
  <h2 class="section-title section-title--sky">PHYSICAL SCIENCES</h2>
  <article class="topic topic--orange"><h3>Forces In Action – Foundation to 6</h3>
    <p>From an apple falling to the ground to a car rolling to a halt, forces are constantly at work. Explore gyroscopes, flying tops, friction and inertia during this stimulating, hands-on look at how things move, and why! Available in a junior or senior format. <span class="states">VIC, NSW, QLD</span></p></article>
  <article class="topic topic--orange"><h3>Rocket Science – Level 3 to 6</h3>
    <p>Brace yourself – we have some exciting rocket science in-store for you! Explore principles of rocket propulsion and the forces involved. Build a sextant in preparation for the grand finale: a water rocket launch up to 30 meters high! Available in a 90 minute format only. <span class="states">VIC, NSW, QLD</span></p></article>
  <article class="topic topic--orange"><h3>Light and Sound – Foundation to Level 2</h3>
    <p>Make some waves, and colour your classroom with rainbows. Using a sensory approach learn all about the properties and transmission of light and sound energy. <span class="states">VIC, NSW, QLD</span></p></article>
  <article class="topic topic--orange"><h3>Electrical Buzz – Foundation to Level 6</h3>
    <p>Lights, noise and airborne propellers. Use snap circuit kits to build exciting circuits using a variety of electrical components including switches, LEDs, resistors and integrated sound circuits. Explore electric motors, electromagnets, dynamos, and energy transformations. Includes a demonstration of how electricity is produced from sun light. <span class="states">VIC, NSW, QLD</span></p></article>
  <article class="topic topic--orange"><h3>Simple Machines – Level 3 to 6</h3>
    <p>Launch projectiles with D.I.Y catapults, watch motorized gears turn to speed things up, and lift friends off the ground with a super-sized lever. An engaging look at how simple machines make our life easier, now, and in the past. Available in a 90 minute format only. <span class="states">VIC</span></p></article>
  <article class="topic topic--orange"><h3>Light &amp; Colour – Foundation to Level 2</h3>
    <p>An engaging investigation into the colourful properties of light. Create rainbows, use chromatography to separate colour in ink, mix colour with light filters and test a whole host of optical instruments. <span class="states">VIC, NSW, QLD</span></p></article>
  <article class="topic topic--orange"><h3>Toy Technology – Foundation to Level 2</h3>
    <p>Be immersed in the wonderful science of toys. Explore energies, materials, movement and sound. Spin some colour, use magnets to draw, and even make your very own balancing toy to take home. Play has never been so educational! <span class="states">VIC, NSW, QLD</span></p></article>
  <article class="topic topic--orange"><h3>Light Reflections – Level 3 to 6</h3>
    <p>This senior primary workshop takes an in-depth look at the properties of light - within and outside the visible spectrum. Get hands-on with a variety of interesting optical instruments, explore UV light and make a UV detection key chain to keep, watch light energy transform, discover different ways to produce light, including chemiluminescence, and more! <span class="states">VIC, NSW, QLD</span></p></article>
  <article class="topic topic--orange"><h3>Heat &amp; Energy – Level 3 to 6</h3>
    <p>Explore the properties of heat and other energies in a fun way. Produce useful heat energy in a multitude of ways, including through friction, motion, electrically and chemically. Transfer heat through conduction, measure it and explore the amazing ways in which heat can generate change. <span class="states">VIC, NSW, QLD</span></p></article>

  <h2 class="section-title section-title--navy" style="margin-top:8px">BIOLOGICAL SCIENCES</h2>
  <article class="topic topic--sky"><h3>Living Things – Foundation to Level 6</h3>
    <p>This workshop is full of life. Explore objects that have self-sustaining processes like plants, animals and mirco-organisms. Through engaging hands-on activities learn about the difference between living and non-living things, simple life cycles and the bigger picture. Available in a junior or senior format. <span class="states">VIC, NSW, QLD</span></p></article>
  <article class="topic topic--sky"><h3>Senses – Foundation to Level 2</h3>
    <p>The five senses are given a workout in this engaging session. They are tested, tricked and more. <span class="states">VIC, NSW, QLD</span></p></article>
  <article class="topic topic--sky"><h3>The Human Body – Level 3 to 6</h3>
    <p>Take a journey through the human body, and explore its parts and systems. Perform chemical experiments to understand digestion, think quick and test reaction speeds, use stethoscopes to listen to the rhythmic beat of your heart. Learn how we are all connected, and made of the stuff of stars! <span class="states">VIC, NSW, QLD</span></p></article>
</section>

<section class="panel panel--right">
  <div class="ocean-photo" role="img" aria-label="Underwater aquarium scene with schools of fish and sharks in blue water"></div>

  <div class="ocean-content">
    <div class="label-box"><h2 class="section-title">EARTH AND SPACE SCIENCES</h2></div>
    <article class="topic"><h3>Wicked Weather – Foundation to Level 2</h3>
      <p>Air in the atmosphere is always on the move, carrying clouds, rain, and snow around the globe. Model and experiment with these air and water movements; and even erupt your own flurry of snow. <span class="states">VIC, NSW, QLD</span></p></article>
    <article class="topic"><h3>Natural Disasters – Level 3 to 6</h3>
      <p>Explore the scientific processes behind the explosive energy of nature’s fury. <span class="states">VIC, NSW, QLD</span></p></article>
    <article class="topic"><h3>Global Sustainability – Level 1 to 6</h3>
      <p>The phenomenal population boom in recent times has put the Earth’s resources under considerable strain. Learn how we can better manage waste and the Earth’s life sustaining resources to build a better future for all. <span class="states">VIC, NSW, QLD</span></p></article>
    <article class="topic"><h3>Earth &amp; The Milky Way – Level 3 to 6</h3>
      <p>Space is a vacuum but it is far from empty. During this fascinating workshop you’ll launch into space and explore planets, moons, stars and galaxies. Follow in the footsteps of the great astronomers as you probe the mystery, scale and Earth’s place in the universe. <span class="states">VIC, NSW, QLD</span></p></article>
    <article class="topic"><h3>Rocks &amp; Geology – Level 3 to 6</h3>
      <p>It is written in the rocks. Read the changing story of Earth and the impact of humans through the pages of rocks. Cast your own fossil, explore and classify rocks and minerals, investigate the characteristics of soil, model the layers of earth, create some explosive lava flows. Everything to enthuse young geologists! <span class="states">VIC</span></p></article>
    <article class="topic"><h3>Water &amp; The Environment – Foundation to Level 4</h3>
      <p>Water is essential to life, and is our most precious resource. We use it to drink, for cooking, washing and hygiene, recreation, industry and agriculture. During this workshop students develop an understanding and appreciation of the importance and special properties of water. <span class="states">VIC, NSW, QLD</span></p></article>
  </div>

  <div class="stem-band">STEM – Science, Technology, Engineering &amp; Mathematics</div>

  <div class="stem-list">
    <article class="topic"><h3>The Power of the Deep Blue – Foundation to Level 6 NEW!</h3>
      <p>Our oceans are teeming with life in various marine environments. They are the heritage, heart and economic future of our country. This workshop takes a deep dive into sustainable seafood and renewable energy production for a marine nation. Available in a junior or senior format. <span class="states">VIC, NSW, QLD</span></p></article>
    <article class="topic"><h3>Hopbot Robotics – Foundation to Level 2</h3>
      <p>An introduction to robots and programming for younger students. With an intuitive interface, colourful hopbot will have learners excited about simple sequencing and directional language. <span class="states">VIC</span></p></article>
    <article class="topic"><h3>kBot Robotics Programming – Level 3 to 6</h3>
      <p>Meet friendly kBOT, a STEM educational robot to learn coding and robotics. Drag-and-drop graphical programming makes learning Codeboard easy and crazy-fun! <strong>Available in a 90 minute format only at $380 plus GST per session.</strong> <span class="states">VIC</span></p></article>
    <article class="topic"><h3>Circuit Board Electronics – Level 5 &amp; 6</h3>
      <p>Solder electronic components onto specially-designed circuit boards. Take home your own working electronic device like an alarm, lie detector or game. Maximum 20 students. <strong>Available in a 90 minute format only at $480 plus GST per session.</strong> <span class="states">VIC</span></p></article>
    <article class="topic"><h3>3D Drawing – Level 1 to 6</h3>
      <p>This STEM workshop has you inventing and creating in 3D. Using 3D pen technology, design your own plastic model to take home. <span class="states">VIC</span></p></article>
    <article class="topic"><h3>WILD SCIENCE SHOW – Foundation to Level 6</h3>
      <p>A jam-packed 60 min show of BIG WOW! science madness! There’s giant smoke vortices, levitating beach balls, flying toilet paper, flour fire-balls, hair-raising electricity, and lots of learning! Suitable for up to 180 students. <strong>Price $650 plus GST.</strong> <span class="states">VIC, NSW, QLD</span></p></article>
  </div>

  <div class="reactive">
    <article class="topic topic--orange"><h3>REACTIVE CHEMISTRY SHOW – Foundation to Level 6 NEW!</h3>
      <p>Watch chemicals react in a big way! See impressive colour changes, smell invisible gasses and hear some oh-mighty noises. Learn about the conversion of reactant molecules to products and the energy changes involved, all while watching shooting foam, hissing fire, and cool blue light. Reactive chemistry at its exciting best! <strong>Price $710 plus GST.</strong> <span class="states">VIC</span></p></article>
  </div>
</section>

</body>
</html>
```